SaaS / Consulting / Solution website redesign

We need a website design that:
- Is completely different than our current design : https://plumvessel.net
- Has a very minimal amount of copy
- Changes our positioning from a SaaS application to a solutions company. Solutions company means that we help our customers solve their problems with consulting, training, and tools. An example of a solutions company is here: https://oldpages.example/web/20130111103320/http://www.brindlework.com:80/
- Does not make us look like a start up
- Is more people oriented than technology oriented

We need a designer that:
- Is a rebel at heart
- Is a minimalist
- Tells us why our current site sucks
- Can disagree with us
- Can also do copywriting or already has a copywriter that can help
- Is ok with saying we have capability that we don't in order to see if people actually want that
- Can understand the difference between our grand vision and where we need to focus ourselves today in order to get there

Who we are:
- Entrepreneurs
- Programmers
- Consultants
- Investors

Here's our design goals:
#1 Get customers, investors, employers, and partners excited about our unique and clearly articulated value proposition
#2 Get people to contact us asking for help with their programs
#3 Position ourselves as an expert in the skills based volunteering, mentorship, and group collaboration
#4 Make it easy for people, who already know who we are, to register online

What our grand vision is:
- Create a marketplace where any person can go to our site and find time with anyone they need to meet with. Whether that is their hair stylist, school advisor, parent of your kids class, dentist, attorney, etc.

What will you get if you win:
- In addition to the prize of this project we will have many landing pages and other revisions we will need in the future. We currently don't have a designer or copywriter and need to add that capability to our team

Who do we need to appeal to:
- Directors that are launching innovative programs inside organizations
- IT personnel who are trying to disqualify our technology so they don't have to support it or deal with it when it doesn't go well
- Enterprise IT architects who don't want our product being on its own island within their organization totally incompatible with everything else. Architects which are trying to assess how our platform will co-exist with all their other platforms
- Vice Presidents who want to help their directors understand that we don't have enough experience to help them
- Program managers who have to juggle a million things and need a tool that actually helps instead of confuses them and adds more work for them.
- Program managers & directors that have been given ambiguous goals by their board of directors like "improve retention, increase engagement, create innovation, get people to collaborate." And who have no idea where to start or how to deliver on things like that.
- Program managers, directors, and vice presidents that are trying to understand how our technology and services fit into their existing technology and capability
- Employees who are bored and uninspired with their current tools and are hoping for some excitement in their life. Kind of like candy or a double espresso.
- Investors who think, our company like all the rest, are going to waste their money and make them look like a fool

Other information:
-The CSS and html needs to be responsive

-Our registration onboarding flow needs to collect this information:
User first name
user last name
user email
(verify their email)
user phone number
(verify their phone number)
User profile image (optional)
User profile summary (optional, like a bio, freeform text fiels)
If applicable: Register their organization
Organization name
Organization image (optional)
Account Mailing address
account Billing address (could be same as mailing address)
account Billing email address (could be same as user address)
account Product selection (pricing tier)
account Credit card information

The designs I am getting are a good start but they are only the front page. I just want you to know that I am expecting and need more than a landing page to complete the design. I will likely need a page that outlines the benefits and features of the product itself, how its different than our competitors, which will not be on the front page. I will need a registration flow. I will need a blog page design so we can post blog articles, I will need a team page, a page that goes into detail on our training, our services. I will likely need a page that shows all news and media we have been in. I need to show customer and user quotes, case studies, a way to contact us, partners, general resources like on collaboration, product tutorials, customers. I need the site to address a comprehensive set of needs. I need that design to be consistent and thorough. I know what PlateHarbor is. I'm not using because I need more than a template that was customized. I need to be unique and match our brand thoughtfully, beautifully, and artistically. Someone asked me a question about how Murmly is similar to our tool in the way it is referred by end users and purchased by managers. Our website needs to primarily talk to the managers as I explained in the brief but it needs to appear cool and exciting to our end-users without focusing on the technology too much. Murmly is a tool that teams use to collaborate in small and large enterprises. The value prop for them is that communication is easier. But they don't put that on their website. Why? Because the users of the technology won't go to the website to find out information on it, they get their information from someone who is using it and demos it to them. When Ines tells her manager Otto "Lets get murmly, Ruth is using it at her company and its great" Ines's manager doesn't know anything about murmly so she promptly googles it. The most important thing from Ines's perspective is that Otto agrees to try it out. Otto's biggest concern is that productivity will be enhanced to degraded. Murmly knows this and so on the front page they know they are talking to Otto NOT Ines because Ines is already sold on it and doesn't need to get sold on the website. Ines is end user. Otto is the purchaser. We have the same problem and so our end users are not the ones purchasing our product, their managers are purchasing our product. We get referred by our end users and vetted by their managers. Hope this helps! Thank you for looking at this project!  Added Wednesday, June 7, 2017

Another observation I am having about the designs being submitted. I believe we used the animations on our current website because animations / cartoons connect with the "inner child" in our users. Whatever that means :-). I think it's what makes our brand fun. I have a hard time imagining that we could make the design fun looking without animations but I'm sure it can be achieved. I also recognize that blending pictures of real people and animations is hard. So either we must masterfully blend them, use only animations, or make the real people have a LOT of fun! So far most of the designs while achieve the goal of appealing to the serious Vice Presidents and directors, they are not doing a good job at appealing to the overworked program managers and bored employees. There seems to stand another challenge with animations which is animations are hard to find and/or create that achieve the message / emotion we are trying to communicate. I don't have any good answers for this but I will say we can hire both animators and illustrators if we need to. All you have to do is communicate the effect in the website design with some simpler version maybe not the end illustration or animation itself. Added Wednesday, June 7, 2017

• Sex appeal and a sense of humor. Copy that makes people excited and clairvoyant about our potential.
• Boring renditions of other non-inspiring websites

```html
<!DOCTYPE html>
<html lang="en">
<head>
<meta charset="utf-8">
<title>Plumvessel — Registration</title>
<link rel="stylesheet" href="https://fonts.googleapis.com/css2?family=Montserrat:wght@400;500;600;700&family=Varela+Round&display=swap">
<style>
  :root {
    --sky: #47b5e6;
    --sky-deep: #3eaee2;
    --sky-faint: #52bbe9;
    --photo-a: #5fa9c9;
    --photo-b: #7fb9cf;
    --ghost: rgba(255,255,255,0.16);
    --ghost-dark: rgba(30,110,160,0.18);
    --white: #ffffff;
    --line: rgba(255,255,255,0.75);
    --mint: #8fd16a;
  }
  * { box-sizing: border-box; margin: 0; padding: 0; }
  html, body { width: 1200px; height: 805px; overflow: hidden; }
  body {
    position: relative;
    background: var(--sky);
    font-family: "Montserrat", sans-serif;
    color: var(--white);
  }

  /* ---------- page underneath the overlay ---------- */
  .page { position: absolute; inset: 0; }
  .hero-photo {
    position: absolute; left: 0; top: 0; width: 1200px; height: 564px;
    background: linear-gradient(110deg, var(--photo-a) 0%, var(--photo-b) 45%, var(--photo-a) 100%);
    opacity: 0.22;
  }
  .hero-arrows { position: absolute; left: 152px; top: 502px; display: flex; gap: 6px; opacity: 0.3; }
  .hero-arrows span {
    width: 22px; height: 22px; border: 1.5px solid var(--white); border-radius: 50%;
    font-size: 12px; line-height: 19px; text-align: center;
  }
  .call-us { position: absolute; left: 690px; top: 25px; font-size: 14px; color: var(--ghost-dark); font-weight: 500; }
  .main-nav {
    position: absolute; left: 456px; top: 83px; display: flex; gap: 40px;
    font-size: 13px; font-weight: 600; color: var(--ghost-dark);
  }
  .audience-card {
    position: absolute; left: 764px; top: 198px; width: 358px; height: 418px;
    background: var(--sky-deep);
  }
  .audience-card h2 {
    position: absolute; left: 42px; top: 48px; width: 280px;
    font-family: "Varela Round", sans-serif; font-weight: 400;
    font-size: 25px; line-height: 35px; color: var(--ghost);
  }
  .audience-card .cta {
    position: absolute; left: 48px; top: 316px; width: 170px;
    font-size: 12px; line-height: 18px; text-align: center; font-weight: 600;
    color: var(--ghost);
  }
  .connect-title {
    position: absolute; left: 0; top: 674px; width: 1200px; text-align: center;
    font-size: 22px; font-weight: 700; color: var(--ghost-dark);
  }
  .timeline { position: absolute; left: 0; top: 710px; }
  .steps {
    position: absolute; top: 772px; left: 0; width: 1200px;
    font-size: 14px; line-height: 17px; color: var(--ghost-dark); text-align: center;
  }
  .steps p { position: absolute; width: 260px; }

  /* ---------- brand & header ---------- */
  .brand {
    position: absolute; left: 77px; top: 42px; display: flex; align-items: center; gap: 12px;
  }
  .brand-dot { width: 44px; height: 44px; border: 4px solid var(--white); border-radius: 50%; }
  .brand-name { font-family: "Varela Round", sans-serif; font-size: 34px; color: var(--white); }
  .register-bar { position: absolute; right: 82px; top: 18px; display: flex; align-items: center; gap: 16px; }
  .register-bar span { font-size: 14px; font-weight: 500; }
  .close-btn {
    width: 32px; height: 32px; border-radius: 50%; background: var(--mint);
    border: 2px solid rgba(255,255,255,0.6);
    display: flex; align-items: center; justify-content: center;
  }

  /* ---------- onboarding step ---------- */
  .onboarding { position: absolute; left: 0; top: 145px; width: 1200px; text-align: center; }
  .onboarding h1 {
    font-family: "Varela Round", sans-serif; font-weight: 400; font-size: 27px; letter-spacing: 0.2px;
  }
  .onboarding .lead { margin-top: 10px; font-size: 14.5px; }
  .field {
    position: absolute; left: 460px; width: 280px; height: 38px;
    border-bottom: 1px solid var(--line);
    font-size: 14px; color: rgba(255,255,255,0.85); text-align: center; line-height: 38px;
  }
  .field.first { top: 256px; }
  .field.last { top: 337px; }
  .next-btn {
    position: absolute; left: 571px; top: 585px; width: 58px; height: 58px;
    border: 1.5px solid var(--white); border-radius: 50%;
    display: flex; align-items: center; justify-content: center;
  }
</style>
</head>
<body>
  <div class="page" aria-hidden="true">
    <div class="hero-photo" role="img" aria-label="Photo of colleagues laughing together at a table"></div>
    <div class="hero-arrows"><span>‹</span><span>›</span></div>
    <div class="call-us">Call Us ✆ 1-800-555-0142</div>
    <nav class="main-nav">
      <span>Company</span><span>Products</span><span>Solutions</span><span>Services &amp; Support</span><span>Industries</span><span>Contact Us</span>
    </nav>
    <div class="audience-card">
      <h2>Vice Presidents who wants to help directors but don't have enough experience to help them!</h2>
      <div class="cta">Get 30 Min Free Consultancy</div>
    </div>
    <div class="connect-title">Get Connected with Plumvessel for</div>
    <svg class="timeline" width="1200" height="30" viewBox="0 0 1200 30">
      <line x1="154" y1="15" x2="1046" y2="15" stroke="#ffffff" stroke-width="1.2"/>
      <circle cx="282" cy="15" r="5.5" fill="#8fd16a" stroke="#ffffff" stroke-width="1.5"/>
      <g fill="#ffffff">
        <circle cx="346" cy="15" r="3"/><circle cx="409" cy="15" r="3"/><circle cx="473" cy="15" r="3"/>
        <circle cx="536" cy="15" r="3"/><circle cx="600" cy="15" r="3"/><circle cx="664" cy="15" r="3"/>
        <circle cx="727" cy="15" r="3"/><circle cx="791" cy="15" r="3"/><circle cx="854" cy="15" r="3"/>
        <circle cx="918" cy="15" r="3"/>
      </g>
    </svg>
    <div class="steps">
      <p style="left:164px">People are drifting apart at work because of</p>
      <p style="left:470px">We're building tools that bring people together</p>
      <p style="left:776px">We're fixing this by meeting people in person</p>
    </div>
  </div>

  <header>
    <div class="brand"><span class="brand-dot"></span><span class="brand-name">Plumvessel</span></div>
    <div class="register-bar">
      <span>Registration</span>
      <div class="close-btn" aria-label="Close">
        <svg width="12" height="12" viewBox="0 0 12 12"><path d="M2 2 L10 10 M10 2 L2 10" stroke="#ffffff" stroke-width="1.8" stroke-linecap="round"/></svg>
      </div>
    </div>
  </header>

  <main>
    <section class="onboarding">
      <h1>Enter your name</h1>
      <p class="lead">Nice to meet you. What's your name?</p>
    </section>
    <div class="field first">First name</div>
    <div class="field last">Last name</div>
    <div class="next-btn" aria-label="Next step">
      <svg width="22" height="14" viewBox="0 0 22 14"><path d="M1 7 H20 M14 1 L20 7 L14 13" fill="none" stroke="#ffffff" stroke-width="1.8" stroke-linecap="round" stroke-linejoin="round"/></svg>
    </div>
  </main>
</body>
</html>
```